Website for legal expungement services with button to qualify/disqualify potential clients

Brightpath Record Renewal, LLC is a law firm focusing in legal expungement servcies (allowing people to erase criminal court records, police records, proseution files, etc). I want a more modern look which exudes confidence in the services. I am looking for a clean website that looks very polished. I want to keep the pages to a minimum, as I want the page not so much to answer questions, but to direct traffic to contact the law office. I would like the main focus point to be an button which would take a client through a series of questions to see if they would qualify for the services; this serves two purposes 1) to collect contact info for future marketing via email and 2) eliminate individuals who we are currently unable to help. A current theme that I have played around with are "Change so much, you'll need to reintroduce yourself" alongside a picture of a guys hand outstretched.
On the landing page, I would like a very brief and to the point explanation of what the service would be (i.e. "Leave your past in the past; expunge all your criminal records" ), followed by a list of benefits that it provides. (NB: included is a file "law post card-02" that includes the main benefits to expungement). Also included are two logo files for a more updated logo I currently use ("BRR Logo" and BRR Logo2") (NB: I'm open to revisions on this as well). Lastly, I've had two very minor 'ads' that I did ("postcard back" and "KVT Ad") that I like the idea of.

Target Market(s)

Middle/upper-middle class, mostly male, people with a criminal record or criminal accusation

Industry/Entity Type

Legal Services

Coding

Coded - Design and coding required

Requirements
Must have
• Button that attracts attention up front (possibly stand out coloring) to click to open up a series of questions to qualify/eliminate prospects, and simultaneously gather their info. Also, must be mobile friendly.

```html
<!DOCTYPE html>
<html lang="en">
<head>
<meta charset="utf-8">
<title>Brightpath Record Renewal</title>
<link href="https://fonts.googleapis.com/css2?family=Lora:wght@500;600&family=Roboto:wght@400;500;700&display=swap" rel="stylesheet">
<style>
:root{
  --navy:#0a3d7c;
  --navy-deep:#062f63;
  --ink:#2f2f2f;
  --text:#6b6b6b;
  --muted:#9a9a9a;
  --dark:#2d2d2d;
  --footer:#323232;
  --line:#d9d9d9;
  --white:#ffffff;
  --panel:#ececec;
}
*{margin:0;padding:0;box-sizing:border-box}
html,body{width:1200px;height:3713px;overflow:hidden}
body{font-family:'Roboto',sans-serif;color:var(--ink);background:var(--white);position:relative}
.abs{position:absolute}

/* top bar */
.topline{left:0;top:0;width:1200px;height:4px;background:var(--dark)}
.top-email{left:665px;top:0;width:270px;height:43px;background:var(--dark);clip-path:polygon(0 0,100% 0,94% 100%,8% 100%);color:#fff;font-size:15px;font-weight:500;display:flex;align-items:center;justify-content:center;gap:10px}
.top-phone{left:918px;top:0;width:282px;height:43px;background:var(--navy);clip-path:polygon(6% 0,100% 0,100% 100%,0 100%);color:#fff;font-size:15px;font-weight:500;display:flex;align-items:center;justify-content:center;gap:10px;padding-left:20px}

/* header */
.brand{left:112px;top:55px;display:flex;align-items:center;gap:22px}
.brand-square{width:39px;height:39px;border:2px solid var(--navy)}
.brand-name{font-family:'Lora',serif;font-weight:500;color:var(--navy);font-size:17px;line-height:21px;letter-spacing:1.5px;text-transform:uppercase}
.nav{left:503px;top:86px;font-size:13px;font-weight:500;color:var(--ink)}
.nav span{position:absolute;white-space:nowrap}
.nav .active{color:var(--navy)}
.social{display:flex;gap:7px}
.social i{width:36px;height:36px;border-radius:50%;background:#fff;box-shadow:0 2px 6px rgba(0,0,0,.2);display:flex;align-items:center;justify-content:center;font-style:normal;font-family:'Roboto',sans-serif;font-weight:700;font-size:13px;color:var(--ink)}
.social i.filled{background:var(--navy);color:#fff}
.header-social{left:966px;top:76px}

/* hero */
.hero{left:0;top:137px;width:1200px;height:617px;
  background:
    radial-gradient(ellipse 170px 130px at 735px 150px,#cfd3d6 0%,rgba(207,211,214,0) 100%),
    radial-gradient(ellipse 280px 260px at 760px 470px,#a9c4dc 0%,rgba(169,196,220,0) 100%),
    radial-gradient(ellipse 120px 200px at 1020px 300px,#d9b7a2 0%,rgba(217,183,162,0) 100%),
    linear-gradient(90deg,#f2f5f8 0%,#e8eef3 42%,#c2d5e5 62%,#dce6ee 85%,#eef2f5 100%)}
.hero-title{left:112px;top:322px;font-family:'Lora',serif;font-weight:600;font-size:35px;line-height:48px;color:var(--ink);text-transform:uppercase}
.btn-solid{background:var(--navy);color:#fff;font-size:14px;font-weight:700;display:flex;align-items:center;justify-content:center;text-transform:uppercase}
.hero-btn{left:112px;top:507px;width:217px;height:48px}

/* section title */
.title{width:1200px;left:0;text-align:center;font-family:'Lora',serif;font-weight:500;font-size:36px;text-transform:uppercase;color:var(--ink)}
.rule{left:523px;width:154px;height:2px;background:var(--line)}
.rule::after{content:"";position:absolute;left:49px;top:-1px;width:56px;height:4px;background:var(--navy)}
.rule.light{background:rgba(255,255,255,.35)}
.rule.light::after{background:#fff}

/* service cards */
.card{top:995px;width:476px;height:575px;background:#fff;box-shadow:0 2px 12px rgba(0,0,0,.15)}
.card .photo{left:8px;top:8px;width:460px;height:327px}
.card h3{left:0;width:100%;top:365px;text-align:center;font-size:20px;font-weight:500;color:var(--ink);text-transform:uppercase}
.card p{left:30px;width:416px;top:406px;text-align:center;font-size:15px;line-height:26px;color:var(--text)}
.btn-outline{left:167px;top:501px;width:141px;height:48px;border:2px solid var(--navy);color:var(--ink);font-size:13px;font-weight:500;display:flex;align-items:center;justify-content:center;text-transform:uppercase}

/* cases */
.cases{left:0;top:1701px;width:1200px;height:442px;background:var(--panel)}
.cases-photo{left:0;top:0;width:620px;height:442px;
  background:
    radial-gradient(ellipse 130px 200px at 140px 230px,#b88b6a 0%,rgba(184,139,106,0) 100%),
    radial-gradient(ellipse 120px 220px at 340px 260px,#2d3444 0%,rgba(45,52,68,0) 100%),
    radial-gradient(ellipse 90px 90px at 330px 110px,#c9a58c 0%,rgba(201,165,140,0) 100%),
    linear-gradient(90deg,#d9cbbd 0%,#c3bdb8 40%,#e2e2e4 75%,#ececec 100%)}
.cases h2{left:617px;top:50px;font-family:'Lora',serif;font-weight:500;font-size:31px;color:var(--ink);text-transform:uppercase}
.cases .short{left:617px;top:95px;width:47px;height:4px;background:var(--navy)}
.cases ul{left:617px;top:136px;width:450px;list-style:none}
.cases li{position:relative;padding-left:34px;font-size:14px;line-height:24px;color:var(--text);margin-bottom:12px}
.cases li svg{position:absolute;left:0;top:5px}
.cases-btn{left:617px;top:336px;width:131px;height:48px}

/* benefits */
.benefits{left:0;top:2143px;width:1200px;height:516px;background:linear-gradient(180deg,var(--navy) 0%,#0b3a74 60%,var(--navy-deep) 100%)}
.benefits .title{top:80px;color:#fff}
.bbox{top:242px;width:231px;height:185px;border:2px solid #fff;color:#fff;font-size:17px;font-weight:700;line-height:28px;text-align:center;text-transform:uppercase;display:flex;align-items:center;justify-content:center;padding:28px 14px 0}
.bicon{top:199px;width:88px;height:87px;background:#fff;display:flex;align-items:center;justify-content:center}
.arrow{top:322px}

/* blog */
.post{top:2858px;width:308px;height:402px;background:#fff;box-shadow:0 1px 4px rgba(0,0,0,.12)}
.post .photo{left:0;top:0;width:308px;height:205px}
.post .edge{right:0;top:215px;width:3px;height:52px;background:var(--navy)}
.post h4{left:17px;top:219px;width:270px;font-size:17px;font-weight:500;line-height:25px;color:var(--ink)}
.post .meta{left:17px;top:282px;display:flex;gap:24px;font-size:13px;color:var(--muted)}
.post .meta span{display:flex;align-items:center;gap:8px}
.post p{left:17px;top:309px;width:274px;font-size:13px;line-height:23px;color:var(--muted);text-align:justify}
.post .more{left:17px;top:378px;font-size:13px;font-weight:700;color:var(--navy);display:flex;align-items:center;gap:8px;text-transform:uppercase}

/* footer */
.footer{left:0;top:3368px;width:1200px;height:295px;background:var(--footer);color:#fff}
.footer .brand{left:470px;top:86px;gap:22px}
.footer .brand-square{border-color:#fff;width:36px;height:36px}
.footer .brand-name{color:#fff;font-size:15px;line-height:18px}
.fnav{left:0;width:1200px;top:158px;text-align:center;font-size:16px;font-weight:500}
.fnav b{font-weight:400;margin:0 24px}
.fcontact{left:0;width:1200px;top:194px;display:flex;justify-content:center;align-items:center;gap:16px;font-size:16px}
.footer .social{left:538px;top:228px}
.footer .social i{width:34px;height:34px}
.legal{left:0;top:3663px;width:1200px;height:50px;background:var(--navy);color:#fff;font-size:12px;font-weight:500;display:flex;align-items:center;justify-content:center}
</style>
</head>
<body>

<div class="abs topline"></div>
<div class="abs top-email">
  <svg width="15" height="11" viewBox="0 0 15 11"><rect width="15" height="11" fill="#fff"/><path d="M0 0 L7.5 6 L15 0" stroke="#2d2d2d" stroke-width="1.4" fill="none"/></svg>
  info@brightpathrr.com
</div>
<div class="abs top-phone">
  <svg width="14" height="14" viewBox="0 0 24 24"><path fill="#fff" d="M6.6 10.8a15.1 15.1 0 0 0 6.6 6.6l2.2-2.2a1 1 0 0 1 1-.25 11.4 11.4 0 0 0 3.6.57 1 1 0 0 1 1 1V20a1 1 0 0 1-1 1A17 17 0 0 1 3 4a1 1 0 0 1 1-1h3.5a1 1 0 0 1 1 1c0 1.25.2 2.45.57 3.6a1 1 0 0 1-.25 1z"/></svg>
  505-555-0148
</div>

<div class="abs brand">
  <div class="brand-square"></div>
  <div class="brand-name">Brightpath<br>Record Renewal</div>
</div>
<nav class="abs nav">
  <span class="active" style="left:0">HOME</span>
  <span style="left:66px">ABOUT US</span>
  <span style="left:158px">SERVICES</span>
  <span style="left:249px">RESOURCES</span>
  <span style="left:354px">CONTACT</span>
</nav>
<div class="abs social header-social"><i class="filled" aria-label="Kova">K</i><i aria-label="Plix">P</i><i aria-label="Rumo">R</i></div>

<div class="abs hero" role="img" aria-label="Smiling businessman in a light blue shirt giving a thumbs up"></div>
<h1 class="abs hero-title">Change so much,<br>you'll need to<br>reintroduce yourself</h1>
<div class="abs btn-solid hero-btn">Book an appointment</div>

<h2 class="abs title" style="top:878px">Our Services</h2>
<div class="abs rule" style="top:931px"></div>

<div class="abs card" style="left:111px">
  <div class="abs photo" role="img" aria-label="Businesswoman shaking hands across a desk" style="background:radial-gradient(ellipse 90px 150px at 140px 170px,#1f2838 0%,rgba(31,40,56,0) 100%),radial-gradient(ellipse 110px 180px at 390px 200px,#9c8d7c 0%,rgba(156,141,124,0) 100%),radial-gradient(ellipse 160px 60px at 200px 290px,#8a6a4f 0%,rgba(138,106,79,0) 100%),linear-gradient(135deg,#3f4751 0%,#7c8389 45%,#b5a99b 100%)"></div>
  <h3 class="abs">Leave your past in the past</h3>
  <p class="abs">Lorem ipsum dolor sit amet, consectetur adipiscing elit, sed do eiusmod tempor incididunt ut labore et dolore magna aliqua ut enim ad minim veniam.</p>
  <div class="abs btn-outline">Learn more</div>
</div>
<div class="abs card" style="left:614px">
  <div class="abs photo" role="img" aria-label="Gavel on a criminal record expungement document" style="background:radial-gradient(ellipse 200px 110px at 300px 210px,#f2eeea 0%,rgba(242,238,234,0) 100%),radial-gradient(ellipse 120px 60px at 330px 50px,#4a2a1c 0%,rgba(74,42,28,0) 100%),radial-gradient(ellipse 70px 40px at 230px 30px,#b8862e 0%,rgba(184,134,46,0) 100%),linear-gradient(135deg,#3a3632 0%,#5e5750 45%,#d9d4cf 75%,#f0ecea 100%)"></div>
  <h3 class="abs">Expunge all your criminal records</h3>
  <p class="abs">Lorem ipsum dolor sit amet, consectetur adipiscing elit, sed do eiusmod tempor incididunt ut labore et dolore magna aliqua ut enim ad minim veniam.</p>
  <div class="abs btn-outline">Learn more</div>
</div>

<section class="abs cases">
  <div class="abs cases-photo" role="img" aria-label="Two business colleagues reviewing a tablet together"></div>
  <h2 class="abs">Types of cases qualify</h2>
  <div class="abs short"></div>
  <ul class="abs">
    <li><svg width="13" height="13" viewBox="0 0 13 13"><circle cx="6.5" cy="6.5" r="6.5" fill="#0a3d7c"/><path d="M4 6.5h4.5M6.5 4.2l2.3 2.3-2.3 2.3" stroke="#fff" stroke-width="1.5" fill="none"/></svg>Lorem ipsum dolor sit amet, consectetur adipiscing elit, sed do eiusmod tempor incididunt ut labore.</li>
    <li><svg width="13" height="13" viewBox="0 0 13 13"><circle cx="6.5" cy="6.5" r="6.5" fill="#0a3d7c"/><path d="M4 6.5h4.5M6.5 4.2l2.3 2.3-2.3 2.3" stroke="#fff" stroke-width="1.5" fill="none"/></svg>Lorem ipsum dolor sit amet, consectetur adipiscing elit, sed do eiusmod tempor incididunt.</li>
    <li><svg width="13" height="13" viewBox="0 0 13 13"><circle cx="6.5" cy="6.5" r="6.5" fill="#0a3d7c"/><path d="M4 6.5h4.5M6.5 4.2l2.3 2.3-2.3 2.3" stroke="#fff" stroke-width="1.5" fill="none"/></svg>Lorem ipsum dolor sit amet, consectetur adipiscing elit, sed do eiusmod tempor incididunt ut labore.</li>
  </ul>
  <div class="abs btn-solid cases-btn">Read more</div>
</section>

<section class="abs benefits">
  <h2 class="abs title">Our Benefits</h2>
  <div class="abs rule light" style="top:130px"></div>

  <svg class="abs arrow" style="left:47px" width="16" height="28" viewBox="0 0 16 28"><path d="M14 2 L3 14 L14 26" stroke="rgba(255,255,255,.45)" stroke-width="3" fill="none"/></svg>
  <svg class="abs arrow" style="left:1136px" width="16" height="28" viewBox="0 0 16 28"><path d="M2 2 L13 14 L2 26" stroke="#fff" stroke-width="3" fill="none"/></svg>

  <div class="abs bbox" style="left:111px">Loan qualification and better loan rates</div>
  <div class="abs bicon" style="left:183px"><svg width="48" height="48" viewBox="0 0 48 48" fill="none" stroke="#333" stroke-width="2"><circle cx="28" cy="18" r="11"/><path d="M28 11v14M31 14h-4.5a2.3 2.3 0 0 0 0 4.6h3a2.3 2.3 0 0 1 0 4.6H25"/><path d="M4 34l8-6h8l6 4h-8M4 42l8-4h14l12-8"/></svg></div>

  <div class="abs bbox" style="left:360px">Protecting your privacy</div>
  <div class="abs bicon" style="left:432px"><svg width="48" height="48" viewBox="0 0 48 48" fill="none" stroke="#333" stroke-width="2"><path d="M24 5l12 5v9c0 8-5 13-12 16-7-3-12-8-12-16v-9z"/><path d="M18 19l4 4 8-8"/><path d="M6 30v10l8 6M42 30v10l-8 6"/></svg></div>

  <div class="abs bbox" style="left:610px">Better education opportunities</div>
  <div class="abs bicon" style="left:682px"><svg width="48" height="48" viewBox="0 0 48 48" fill="none" stroke="#333" stroke-width="2"><circle cx="18" cy="18" r="10"/><circle cx="18" cy="18" r="4"/><path d="M26 10l14-6M34 4h6v6"/><rect x="22" y="30" width="20" height="12"/><path d="M28 30v-3h8v3"/><rect x="6" y="32" width="10" height="10"/></svg></div>

  <div class="abs bbox" style="left:859px">Lower insurance premiums</div>
  <div class="abs bicon" style="left:931px"><svg width="48" height="48" viewBox="0 0 48 48" fill="none" stroke="#333" stroke-width="2"><rect x="8" y="8" width="24" height="34" rx="2"/><path d="M16 5h8v6h-8z"/><path d="M12 18l2 2 4-4M12 28l2 2 4-4M21 18h7M21 28h5"/><path d="M34 24l8 3v6c0 5-4 8-8 10-4-2-8-5-8-10v-6z"/><path d="M31 33l2 2 4-4"/></svg></div>
</section>

<h2 class="abs title" style="top:2758px">Latest Blog</h2>
<div class="abs rule" style="top:2811px"></div>

<article class="abs post" style="left:111px">
  <div class="abs photo" role="img" aria-label="Business team shaking hands in an office" style="background:radial-gradient(ellipse 60px 110px at 60px 120px,#243450 0%,rgba(36,52,80,0) 100%),radial-gradient(ellipse 70px 120px at 250px 130px,#1d2533 0%,rgba(29,37,51,0) 100%),radial-gradient(ellipse 60px 80px at 170px 110px,#c9b2a2 0%,rgba(201,178,162,0) 100%),linear-gradient(135deg,#b7c5d3 0%,#8796a8 50%,#4a5870 100%)"></div>
  <div class="abs edge"></div>
  <h4 class="abs">Lorem ipsum dolor sit amet, con sectetur adipiscing</h4>
  <div class="abs meta"><span><svg width="11" height="12" viewBox="0 0 11 12"><circle cx="5.5" cy="3" r="3" fill="#0a3d7c"/><path d="M0 12a5.5 5 0 0 1 11 0z" fill="#0a3d7c"/></svg>Daniel Reyes</span><span><svg width="12" height="12" viewBox="0 0 12 12"><rect y="2" width="12" height="10" fill="#999"/><rect x="1.5" y="5" width="9" height="5.5" fill="#fff"/></svg>08 May 2023</span></div>
  <p class="abs">Lorem ipsum dolor sit amet, consectetur adipiscing elit, sed do eiusmod tempor incidi dunt ut labore et dolore magna aliqua.</p>
  <div class="abs more">Read more <svg width="12" height="12" viewBox="0 0 13 13"><circle cx="6.5" cy="6.5" r="6.5" fill="#0a3d7c"/><path d="M4 6.5h4.5M6.5 4.2l2.3 2.3-2.3 2.3" stroke="#fff" stroke-width="1.5" fill="none"/></svg></div>
</article>

<article class="abs post" style="left:445px">
  <div class="abs photo" role="img" aria-label="Two professionals reviewing a tablet" style="background:radial-gradient(ellipse 90px 40px at 170px 95px,#d8dde3 0%,rgba(216,221,227,0) 100%),radial-gradient(ellipse 60px 50px at 140px 150px,#c49c84 0%,rgba(196,156,132,0) 100%),linear-gradient(135deg,#1b2840 0%,#2f4160 50%,#6e7f96 100%)"></div>
  <div class="abs edge"></div>
  <h4 class="abs">Lorem ipsum dolor sit amet, con sectetur adipiscing</h4>
  <div class="abs meta"><span><svg width="11" height="12" viewBox="0 0 11 12"><circle cx="5.5" cy="3" r="3" fill="#0a3d7c"/><path d="M0 12a5.5 5 0 0 1 11 0z" fill="#0a3d7c"/></svg>Daniel Reyes</span><span><svg width="12" height="12" viewBox="0 0 12 12"><rect y="2" width="12" height="10" fill="#999"/><rect x="1.5" y="5" width="9" height="5.5" fill="#fff"/></svg>08 May 2023</span></div>
  <p class="abs">Lorem ipsum dolor sit amet, consectetur adipiscing elit, sed do eiusmod tempor incidi dunt ut labore et dolore magna aliqua.</p>
  <div class="abs more">Read more <svg width="12" height="12" viewBox="0 0 13 13"><circle cx="6.5" cy="6.5" r="6.5" fill="#0a3d7c"/><path d="M4 6.5h4.5M6.5 4.2l2.3 2.3-2.3 2.3" stroke="#fff" stroke-width="1.5" fill="none"/></svg></div>
</article>

<article class="abs post" style="left:780px">
  <div class="abs photo" role="img" aria-label="Two businessmen in conversation at a meeting" style="background:radial-gradient(ellipse 80px 120px at 100px 140px,#1c2433 0%,rgba(28,36,51,0) 100%),radial-gradient(ellipse 70px 130px at 250px 140px,#222a38 0%,rgba(34,42,56,0) 100%),linear-gradient(135deg,#f0f2f4 0%,#c7ced6 45%,#6b7788 100%)"></div>
  <div class="abs edge"></div>
  <h4 class="abs">Lorem ipsum dolor sit amet, con sectetur adipiscing</h4>
  <div class="abs meta"><span><svg width="11" height="12" viewBox="0 0 11 12"><circle cx="5.5" cy="3" r="3" fill="#0a3d7c"/><path d="M0 12a5.5 5 0 0 1 11 0z" fill="#0a3d7c"/></svg>Daniel Reyes</span><span><svg width="12" height="12" viewBox="0 0 12 12"><rect y="2" width="12" height="10" fill="#999"/><rect x="1.5" y="5" width="9" height="5.5" fill="#fff"/></svg>08 May 2023</span></div>
  <p class="abs">Lorem ipsum dolor sit amet, consectetur adipiscing elit, sed do eiusmod tempor incidi dunt ut labore et dolore magna aliqua.</p>
  <div class="abs more">Read more <svg width="12" height="12" viewBox="0 0 13 13"><circle cx="6.5" cy="6.5" r="6.5" fill="#0a3d7c"/><path d="M4 6.5h4.5M6.5 4.2l2.3 2.3-2.3 2.3" stroke="#fff" stroke-width="1.5" fill="none"/></svg></div>
</article>

<footer class="abs footer">
  <div class="abs brand">
    <div class="brand-square"></div>
    <div class="brand-name">Brightpath<br>Record Renewal</div>
  </div>
  <div class="abs fnav">HOME<b>|</b>ABOUT US<b>|</b>SERVICES<b>|</b>RESOURCES<b>|</b>CONTACT</div>
  <div class="abs fcontact">
    <span style="display:flex;align-items:center;gap:10px"><svg width="14" height="14" viewBox="0 0 24 24"><path fill="#fff" d="M6.6 10.8a15.1 15.1 0 0 0 6.6 6.6l2.2-2.2a1 1 0 0 1 1-.25 11.4 11.4 0 0 0 3.6.57 1 1 0 0 1 1 1V20a1 1 0 0 1-1 1A17 17 0 0 1 3 4a1 1 0 0 1 1-1h3.5a1 1 0 0 1 1 1c0 1.25.2 2.45.57 3.6a1 1 0 0 1-.25 1z"/></svg>505-555-0148</span>
    <span>|</span>
    <span style="display:flex;align-items:center;gap:10px"><svg width="15" height="11" viewBox="0 0 15 11"><rect width="15" height="11" fill="#fff"/><path d="M0 0 L7.5 6 L15 0" stroke="#323232" stroke-width="1.4" fill="none"/></svg>info@brightpathrr.com</span>
  </div>
  <div class="abs social"><i class="filled" aria-label="Kova">K</i><i aria-label="Plix">P</i><i aria-label="Rumo">R</i></div>
</footer>
<div class="abs legal">© 2023 BRIGHTPATH RECORD RENEWAL &nbsp;&nbsp;|&nbsp;&nbsp; All Rights Reserved</div>

</body>
</html>
```